Lawn care business card

I am looking for a quality designed personal business card to represent the quality and elegant nature of our company. We separate ourselves in our market by the aesthetic value of our work, so I am looking for marketing material that does the same. We target our marketing high end customers, and we try to avoid price shoppers. I am open to all design options, so long as they are in line with our companies values.

We are tend to go with a retro look on everything from our logo and print material, to our uniforms. We like to portray and "old fashion" set of core values, with a modern elegance. So a wild and crazy look is out of the question.

Things I'd like on the card:
1.) Logo
2.) Phone number: (816) 555-2931
3.) Website: Verdelynkc.com
4.) Email: robertfairley@verdelynkc.com
5.) My name: Robert Fairley
6.) Facebook link: facebook.com/VerdelynGardenandGrounds
7.) Instagram: http://instagram.com/verdelynkc

Attached is a copy of our logo.

Reason: More time is needed to gather conclusive feedback from the members of our marketing team.

```html
<!DOCTYPE html>
<html lang="en">
<head>
<meta charset="utf-8">
<title>Verdelyn Business Card</title>
<link rel="stylesheet" href="https://fonts.googleapis.com/css2?family=Arimo:wght@400;700&display=swap">
<style>
  :root {
    --ink: #1c1c1c;
    --paper: #ffffff;
    --accent: #e8581c;
    --backdrop: #ececec;
    --text-dark: #161616;
  }
  * { box-sizing: border-box; margin: 0; padding: 0; }
  html, body {
    width: 1200px;
    height: 864px;
    overflow: hidden;
    background: var(--backdrop);
    font-family: "Arimo", Arial, sans-serif;
  }
  .card {
    position: absolute;
    left: 75px;
    top: 132px;
    width: 1050px;
    height: 600px;
    background: var(--paper);
    display: grid;
    grid-template-rows: 210px 270px 120px;
    box-shadow: 0 10px 30px rgba(0,0,0,0.18);
  }
  .band-top {
    background: var(--ink);
    display: flex;
    flex-direction: column;
    align-items: flex-end;
    justify-content: flex-end;
    padding: 0 60px 30px 0;
  }
  .holder-name {
    color: var(--accent);
    font-size: 46px;
    font-weight: 400;
    letter-spacing: 1.5px;
  }
  .holder-phone {
    color: var(--paper);
    font-size: 24px;
    letter-spacing: 1px;
    margin-top: 6px;
  }
  .band-middle {
    display: flex;
    align-items: center;
    padding: 0 50px 0 70px;
  }
  .brand {
    display: flex;
    align-items: center;
    gap: 16px;
    width: 400px;
    flex: none;
  }
  .brand-dot {
    width: 34px;
    height: 34px;
    border-radius: 50%;
    background: var(--accent);
    flex: none;
  }
  .brand-name {
    color: var(--ink);
    font-size: 54px;
    font-weight: 700;
    letter-spacing: 2px;
  }
  .contact-list {
    list-style: none;
    display: flex;
    flex-direction: column;
    gap: 14px;
  }
  .contact-item {
    display: flex;
    align-items: center;
    gap: 16px;
    color: var(--text-dark);
    font-size: 26px;
    letter-spacing: 1px;
    white-space: nowrap;
  }
  .contact-icon {
    width: 24px;
    height: 24px;
    flex: none;
  }
  .band-bottom {
    background: var(--ink);
    display: flex;
    align-items: center;
    justify-content: center;
  }
  .social-link {
    color: var(--accent);
    font-size: 32px;
    letter-spacing: 1.5px;
    white-space: nowrap;
  }
</style>
</head>
<body>
  <div class="card">
    <header class="band-top">
      <div class="holder-name">Robert Fairley</div>
      <div class="holder-phone">(816) 555-2931</div>
    </header>

    <section class="band-middle">
      <div class="brand">
        <span class="brand-dot"></span>
        <span class="brand-name">Verdelyn</span>
      </div>
      <ul class="contact-list">
        <li class="contact-item">
          <svg class="contact-icon" viewBox="0 0 24 24" aria-hidden="true">
            <rect width="24" height="24" fill="var(--accent)"/>
            <circle cx="12" cy="12" r="7" fill="none" stroke="#fff" stroke-width="1.6"/>
            <ellipse cx="12" cy="12" rx="3" ry="7" fill="none" stroke="#fff" stroke-width="1.4"/>
            <line x1="5" y1="12" x2="19" y2="12" stroke="#fff" stroke-width="1.4"/>
          </svg>
          <span>Verdelynkc.com</span>
        </li>
        <li class="contact-item">
          <svg class="contact-icon" viewBox="0 0 24 24" aria-hidden="true">
            <rect width="24" height="24" fill="var(--accent)"/>
            <rect x="5" y="7" width="14" height="10" fill="none" stroke="#fff" stroke-width="1.6"/>
            <polyline points="5,7 12,13 19,7" fill="none" stroke="#fff" stroke-width="1.6"/>
          </svg>
          <span>robertfairley@verdelynkc.com</span>
        </li>
        <li class="contact-item">
          <svg class="contact-icon" viewBox="0 0 24 24" aria-hidden="true">
            <rect width="24" height="24" fill="var(--accent)"/>
          </svg>
          <span>http://photoleaf.net/verdelynkc</span>
        </li>
      </ul>
    </section>

    <footer class="band-bottom">
      <span class="social-link">greenlinkpages.net/VerdelynGardenandGrounds</span>
    </footer>
  </div>
</body>
</html>
```